Letterhead and matching envelope design for a dental office

We need a new stationary design, letterhead and envelope #10, for a dental office in Denver area. We are called Bright Harbor Dental. We want a simple and minimalistic design but not a boring design. I wish to have one good point that makes it look professional. I have attached our logo. Feel free to use either one. I want the design for letterhead and envelope look like a "matching pair" but not look the same. The envelope doesn't have to be white and it will have an address window on bottom left.

Target Market(s)

everyone who visits dentist (adults)

Industry/Entity Type

Dental

Font styles to use
Other font styles liked:
• close to font on logo or something that matches well

Requirements
Must have
• professional
• simple, minimalistic
• unique point that stands out
Nice to have
• matching but not same design for letterhead and envelope
Should not have
• not look like all the other boring designs
• no flowery, distracting feats

```html
<!DOCTYPE html>
<html lang="en">
<head>
<meta charset="utf-8">
<title>Bright Harbor Dental – Letterhead</title>
<link href="https://fonts.googleapis.com/css2?family=Open+Sans:wght@400;600;700&display=swap" rel="stylesheet">
<style>
  :root {
    --backdrop: #e9e9ea;
    --paper: #ffffff;
    --ink: #3a3a3a;
    --ink-soft: #555555;
    --brand-green: #3bb54a;
    --brand-green-light: #a9dcaa;
    --signature-tone: #d9d9d9;
  }
  * { box-sizing: border-box; margin: 0; padding: 0; }
  html, body {
    width: 1200px; height: 795px; overflow: hidden;
    background: var(--backdrop);
    font-family: "Open Sans", Arial, sans-serif;
  }
  .letterhead {
    position: absolute;
    left: 338px; top: 27px;
    width: 523px; height: 740px;
    background: var(--paper);
    box-shadow: 0 2px 10px rgba(0,0,0,0.12);
    overflow: hidden;
    color: var(--ink);
  }
  .brand {
    position: absolute; left: 42px; top: 52px;
    display: flex; align-items: center; gap: 7px;
  }
  .brand-dot {
    width: 12px; height: 12px; border-radius: 50%;
    background: var(--brand-green);
  }
  .brand-name {
    font-size: 13px; font-weight: 600; color: var(--brand-green);
    letter-spacing: 0.3px;
  }
  .contact {
    position: absolute; left: 330px; top: 40px;
    font-size: 7px; line-height: 1.45; color: var(--ink);
  }
  .contact-row { display: flex; align-items: center; gap: 4px; }
  .contact-icon {
    width: 8px; height: 8px; border-radius: 50%;
    background: var(--brand-green);
    display: inline-flex; align-items: center; justify-content: center;
  }
  .contact-icon svg { width: 5px; height: 5px; }
  .letter-body {
    position: absolute; left: 42px; top: 198px; width: 430px;
    font-size: 7.4px; line-height: 1.4; color: var(--ink-soft);
  }
  .salutation {
    font-size: 9px; font-weight: 700; color: var(--ink);
    margin-bottom: 8px;
  }
  .letter-body p { margin-bottom: 9px; }
  .signature {
    margin-top: 18px; width: 92px; height: 30px;
    background: var(--signature-tone); border-radius: 3px;
  }
  .footer-swoosh {
    position: absolute; left: 0; bottom: 0; width: 523px; height: 230px;
  }
</style>
</head>
<body>
  <main class="letterhead">
    <header>
      <div class="brand">
        <span class="brand-dot"></span>
        <span class="brand-name">Bright Harbor Dental</span>
      </div>
      <address class="contact" style="font-style:normal">
        <div>2280 Lakeview Blvd,</div>
        <div>Suite 210 Arvada, CO 80004</div>
        <div class="contact-row">
          <span class="contact-icon"><svg viewBox="0 0 10 10"><path d="M2 1h2l1 2.5-1.2.8a6 6 0 0 0 2.9 2.9l.8-1.2L10 7v2c-5 .5-9-3.5-8-8z" fill="#fff"/></svg></span>
          <span>303-555-0148</span>
        </div>
        <div class="contact-row">
          <span class="contact-icon"><svg viewBox="0 0 10 10"><rect x="1" y="2.5" width="8" height="5" fill="none" stroke="#fff" stroke-width="1.2"/><path d="M1 2.5l4 3 4-3" fill="none" stroke="#fff" stroke-width="1.2"/></svg></span>
          <span>hello@brightharbordental.com</span>
        </div>
        <div class="contact-row">
          <span class="contact-icon"><svg viewBox="0 0 10 10"><circle cx="5" cy="5" r="3.8" fill="none" stroke="#fff" stroke-width="1.1"/><path d="M1.2 5h7.6M5 1.2c-2 2.4-2 5.2 0 7.6M5 1.2c2 2.4 2 5.2 0 7.6" fill="none" stroke="#fff" stroke-width="0.9"/></svg></span>
          <span>www.brightharbordental.com</span>
        </div>
      </address>
    </header>

    <section class="letter-body">
      <p class="salutation">Dear Mr. Ellison,</p>
      <p>Lorem Ipsum is simply dummy text of the printing and typesetting industry. Lorem Ipsum has been the industry's standard dummy text ever since the 1500s, when an unknown printer took a galley of type and scrambled it to make a type specimen book. It has survived not only five centuries, but also the leap into electronic typesetting, remaining essentially unchanged.</p>
      <p>The standard chunk of Lorem Ipsum used since the 1500s is reproduced below for those interested. Sections 1.10.32 and 1.10.33 from "de Finibus Bonorum et Malorum" by Cicero are also reproduced in their exact original form, accompanied by English versions from the 1914 translation by H. Rackham.</p>
      <p>Lorem Ipsum is simply dummy text of the printing and typesetting industry. Lorem Ipsum has been the industry's standard dummy text ever since the 1500s, when an unknown printer took a galley of type and scrambled it to make a type specimen book. It has survived not only five centuries, but also the leap into electronic typesetting, remaining essentially unchanged. It was popularised in the</p>
      <div class="signature" role="img" aria-label="Handwritten signature of the sender"></div>
    </section>

    <svg class="footer-swoosh" viewBox="0 0 523 230" preserveAspectRatio="none" aria-hidden="true">
      <path d="M0 205 C190 196 410 150 523 0 L523 230 L0 230 Z" fill="var(--brand-green-light)"/>
      <path d="M0 214 C200 206 420 165 523 26 L523 230 L0 230 Z" fill="var(--paper)"/>
      <path d="M0 219 C205 212 428 175 523 40 L523 230 L0 230 Z" fill="var(--brand-green)"/>
    </svg>
  </main>
</body>
</html>
```